Diverse, up-scale salon needs eye-catching, unique business cards.

We are looking for a unique business card design for our stylist but that can also be multi functional and used for appointment reminder and referrals. I will need a design in a format that I can modify names and titles going forward. In the past we have had a dark background with the logo on one side, and stylist and contact information on the other but we are open to all ideas. I have included our mission statement as well as branded colors below. The statement doesn't need to go on the card, it's just a reference for target market. We need space for the stylists name, title, instagram handle and then the salons phone number, website and address. I am also open to adding a spot for a qr code linked to the stylist instagram or the salon booking link.

primary brand colors:
#333333 #233415 #36502a #93874a #000000
Mission statement:
Vessolin Hair Studio, a high-end salon located in the lively Downtown Farmington, Michigan, is committed to providing exceptional services in a welcoming and relaxed environment to meet the needs of our diverse clientele.
Our salon specializes in contemporary custom haircuts, coloring, extensions, and barbering and beard grooming services. Our team of skilled stylists is passionate and inventive in their hair styling techniques. At the heart of our salon are values centered on quality, innovation, creativity, and above all, comfort. These core values are evident in every appointment across our customizable array of services.
Our goal is to establish a benchmark for exceptional hair care for every human.
Website: www.vessolinhairstudio.example
instagram: @vessolinhairstudio
address: 41782 Pelham Crest Rd, Farmington MI
phone: 248-613-4087

Industry/Entity Type

Hair Salon

Contact Information for Business Card

Stylist name, title, phone, instagram, website, address, (optional qr code)

Requirements
Should not have
• Does not need mission statement on the card.

```html
<!DOCTYPE html>
<html lang="en">
<head>
<meta charset="utf-8">
<title>Vessolin Hair Studio — Business Card</title>
<link rel="stylesheet" href="https://fonts.googleapis.com/css2?family=Montserrat:wght@400;500;600;700&display=swap">
<style>
  :root {
    --page-bg: #e6e2db;
    --card-black: #000000;
    --card-charcoal: #333333;
    --gold: #93874a;
    --gold-light: #a8965a;
    --text-soft: #cfcac1;
  }
  * { box-sizing: border-box; margin: 0; padding: 0; }
  html, body {
    width: 1200px; height: 1200px; overflow: hidden;
    background: var(--page-bg);
  }
  .canvas {
    position: relative; width: 1200px; height: 1200px;
    font-family: "Montserrat", sans-serif;
  }
  .business-card {
    position: absolute; left: 80px; top: 318px;
    width: 1040px; height: 565px;
    border-radius: 30px; overflow: hidden;
    background:
      radial-gradient(ellipse 55% 70% at 38% 45%, rgba(51,51,51,0.55), transparent 70%),
      linear-gradient(100deg, #141414 0%, #1d1d1d 35%, var(--card-black) 75%);
  }
  .edge-tab {
    position: absolute; left: 0; top: 78px;
    width: 14px; height: 52px;
    background: var(--gold); border-radius: 0 8px 8px 0;
  }
  .stylist-name {
    position: absolute; left: 63px; top: 62px;
    font-size: 35px; font-weight: 600; letter-spacing: 1.5px;
    color: var(--gold-light); text-transform: uppercase;
  }
  .stylist-title {
    position: absolute; left: 63px; top: 112px;
    font-size: 25px; font-weight: 500; color: var(--text-soft);
  }
  .salon-address {
    position: absolute; left: 63px; top: 240px;
    font-size: 25px; font-weight: 400; line-height: 40px;
    color: var(--text-soft); font-style: normal;
  }
  .contact-list {
    position: absolute; left: 63px; top: 376px; list-style: none;
  }
  .contact-item {
    display: flex; align-items: center; gap: 14px;
    height: 40px; font-size: 25px; color: var(--text-soft);
  }
  .contact-icon { width: 24px; height: 24px; flex: none; }
  .brand-mark {
    position: absolute; left: 500px; top: 40px;
    width: 480px; height: 480px;
    display: flex; flex-direction: column; align-items: center; justify-content: center;
  }
  .brand-ring {
    width: 320px; height: 320px; border-radius: 50%;
    border: 7px solid var(--gold);
  }
  .brand-name {
    margin-top: 34px;
    font-size: 36px; font-weight: 600; letter-spacing: 4px;
    text-transform: uppercase; color: var(--gold-light);
    text-align: center;
  }
</style>
</head>
<body>
<main class="canvas">
  <section class="business-card" aria-label="Vessolin Hair Studio business card">
    <span class="edge-tab"></span>

    <h1 class="stylist-name">Marlowe Quinn</h1>
    <p class="stylist-title">President</p>

    <address class="salon-address">
      41782 Pelham Crest Rd<br>
      Farmington MI
    </address>

    <ul class="contact-list">
      <li class="contact-item">
        <svg class="contact-icon" viewBox="0 0 24 24" aria-hidden="true">
          <path d="M6.6 10.8c1.4 2.8 3.8 5.1 6.6 6.6l2.2-2.2c.3-.3.7-.4 1-.2 1.1.4 2.3.6 3.6.6.6 0 1 .4 1 1V20c0 .6-.4 1-1 1C10.6 21 3 13.4 3 4c0-.6.4-1 1-1h3.5c.6 0 1 .4 1 1 0 1.3.2 2.5.6 3.6.1.3 0 .7-.2 1z" fill="none" stroke="#a8965a" stroke-width="1.8" stroke-linejoin="round"/>
        </svg>
        <span>248-613-4087</span>
      </li>
      <li class="contact-item">
        <svg class="contact-icon" viewBox="0 0 24 24" aria-hidden="true">
          <circle cx="12" cy="12" r="8.5" fill="none" stroke="#a8965a" stroke-width="1.8"/>
        </svg>
        <span>@vessolinhairstudio</span>
      </li>
      <li class="contact-item">
        <svg class="contact-icon" viewBox="0 0 24 24" aria-hidden="true">
          <g fill="none" stroke="#a8965a" stroke-width="1.6">
            <circle cx="12" cy="12" r="9"/>
            <ellipse cx="12" cy="12" rx="4" ry="9"/>
            <line x1="3" y1="12" x2="21" y2="12"/>
          </g>
        </svg>
        <span>www.vessolinhairstudio.example</span>
      </li>
    </ul>

    <div class="brand-mark">
      <span class="brand-ring" aria-hidden="true"></span>
      <p class="brand-name">Vessolin Hair Studio</p>
    </div>
  </section>
</main>
</body>
</html>
```